Business Card for Beach theme sports bar called MORVIN

I need a business card designed for our employees, front and back. This will be used by the employees of two business locations to hand out to customers. I've attached the previous business cards we used at one time for a Dantells (it is now Morvin). Looking for a fresh new card that is elegant but has character.

Target Market(s)

30-60, middle class

Contact Information for Business Card

We are a beach bar and sports bar. I am looking for an elegant business card with the front to have the MORVIN logo. Then on the back I need it to allow a space for employees to write their names and for them to write in their schedule. I have attached our old cards with our old name Dantells so you can pull everything we need on the cards. one thing is missing is we have another location at 2615 W Calder Ridge Rd with a number of 702-418-9053. Since we will use it for both locations it should allow the employee to circle or check mark the bar which they work at.

Font styles to use
Sans Serif

Requirements
Must have
• We are looking for some fresh ideas for the business card. Something that will really stick out to customers when the staff hands them out. Creativity will be looked at positively, but we still want it to look upscale and fun.

```html
<!DOCTYPE html>
<html lang="en">
<head>
<meta charset="utf-8">
<title>Morvin Business Card</title>
<link rel="stylesheet" href="https://fonts.googleapis.com/css2?family=Arimo:wght@400;700&family=Tinos:ital@0;1&display=swap">
<style>
  :root {
    --page-bg: #bdbdbd;
    --card-bg: #262626;
    --card-pattern-dark: #1e1e1e;
    --card-pattern-light: #3a3a3a;
    --accent-red: #e0282a;
    --accent-yellow: #ffcc00;
    --text-light: #ffffff;
    --watermark: #333333;
  }
  * { margin: 0; padding: 0; box-sizing: border-box; }
  html, body {
    width: 1200px; height: 1200px; overflow: hidden;
    background: var(--page-bg);
  }
  .card {
    position: absolute; left: 250px;
    width: 707px; height: 404px;
    background: var(--card-bg);
    color: var(--text-light);
    overflow: hidden;
  }
  .card--front { top: 144px; }
  .card--back { top: 582px; }

  .front-pattern {
    position: absolute; inset: 0;
    background: linear-gradient(90deg, var(--card-pattern-dark) 0%, var(--card-bg) 50%, var(--card-pattern-light) 100%);
  }
  .brand-name {
    position: absolute; left: 0; right: 0; top: 140px;
    text-align: center;
    font: 700 112px/1 "Arimo", sans-serif;
    color: var(--text-light);
  }
  .tagline {
    position: absolute; left: 0; right: 0; top: 317px;
    text-align: center;
    font: 400 31px/1 "Tinos", serif;
    color: var(--accent-red);
    letter-spacing: 0.5px;
  }

  .offer-title {
    position: absolute; left: 20px; top: 28px;
    font: 700 82px/1 "Arimo", sans-serif;
    color: var(--accent-yellow);
    white-space: nowrap;
    letter-spacing: -0.5px;
  }
  .watermark-name {
    position: absolute; left: 22px; top: 238px;
    font: 700 112px/1 "Arimo", sans-serif;
    color: var(--watermark);
  }
  .field-label {
    position: absolute; left: 37px; top: 117px;
    font: 700 37px/1 "Arimo", sans-serif;
    letter-spacing: 1px;
  }
  .name-box {
    position: absolute; left: 38px; top: 166px;
    width: 224px; height: 57px;
    border: 3px solid var(--text-light);
  }
  .schedule {
    position: absolute; left: 311px; top: 141px;
    width: 352px;
  }
  .schedule__days {
    display: flex;
    font: 700 24px/1 "Arimo", sans-serif;
    margin-bottom: 9px;
  }
  .schedule__days span { flex: 1; text-align: center; }
  .schedule__boxes {
    display: flex; height: 42px;
    border: 3px solid var(--text-light);
  }
  .schedule__boxes span { flex: 1; border-right: 3px solid var(--text-light); }
  .schedule__boxes span:last-child { border-right: none; }

  .location {
    position: absolute;
    text-align: center;
    font: 400 20px/27px "Tinos", serif;
  }
  .location--one { left: 60px; width: 240px; top: 270px; }
  .location--two { left: 400px; width: 270px; top: 257px; }
  .fine-print {
    position: absolute; left: 0; right: 0; top: 369px;
    text-align: center;
    font: italic 400 12px/1 "Tinos", serif;
  }
</style>
</head>
<body>
  <section class="card card--front">
    <div class="front-pattern" role="img" aria-label="Repeating palm frond pattern fading from dark to lighter grey"></div>
    <div class="brand-name">Morvin</div>
    <div class="tagline">A Gamers Bar</div>
  </section>

  <section class="card card--back">
    <div class="watermark-name" aria-hidden="true">Morvin</div>
    <h1 class="offer-title">$20 MATCH PLAY</h1>
    <div class="field-label">Bartender</div>
    <div class="name-box"></div>
    <div class="schedule">
      <div class="schedule__days">
        <span>M</span><span>T</span><span>W</span><span>Th</span><span>F</span><span>Sa</span><span>Su</span>
      </div>
      <div class="schedule__boxes">
        <span></span><span></span><span></span><span></span><span></span><span></span><span></span>
      </div>
    </div>
    <address class="location location--one" style="font-style:normal">
      2615 W Calder Ridge Rd<br>702-418-9053
    </address>
    <address class="location location--two" style="font-style:normal">
      3388 W Harlow Crest Rd<br>Las Vegas, NV 89146<br>702-631-4728<br>cs@morvinbar.com
    </address>
    <p class="fine-print">Match play for new slot members, must play total 100 coin.&nbsp; Please see bartender for details.&nbsp; Management reserves all rights</p>
  </section>
</body>
</html>
```